Business Card for a New Zealand IT Startup

I need a business card for VELTA Holdings. We are a young startup based in New Zealand working in internet marketing and web development. The design should have some element connected to New Zealand, such as wave, koru or silver fern, just don't use a kiwi bird.

```html
<!DOCTYPE html>
<html lang="en">
<head>
<meta charset="utf-8">
<title>VELTA Holdings – Business Card</title>
<link href="https://fonts.googleapis.com/css2?family=Open+Sans:wght@400;600;700&display=swap" rel="stylesheet">
<style>
  :root {
    --brand-blue: #0a6cbd;
    --brand-blue-dark: #075a9f;
    --brand-orange: #e0541c;
    --brand-orange-dark: #b9441a;
    --card-white: #ffffff;
    --text-dark: #2f2f2f;
    --page-bg: #e9eaec;
  }
  * { margin: 0; padding: 0; box-sizing: border-box; }
  html, body {
    width: 1200px; height: 1000px; overflow: hidden;
    background: var(--page-bg);
    font-family: "Open Sans", sans-serif;
  }
  .sheet {
    position: relative; width: 1200px; height: 1000px;
  }
  .card {
    position: absolute; left: 250px; width: 700px; height: 400px;
    overflow: hidden; border-radius: 4px;
    box-shadow: 0 10px 30px rgba(0,0,0,0.18);
  }
  .card--back { top: 60px; background: var(--brand-blue); }
  .card--front { top: 540px; background: var(--card-white); }
  .card__shapes { position: absolute; inset: 0; width: 100%; height: 100%; }

  /* back side */
  .back-mark {
    position: absolute; left: 0; right: 0; top: 140px;
    display: flex; align-items: center; justify-content: center; gap: 18px;
    color: var(--card-white);
    font-weight: 700; font-size: 44px; letter-spacing: 1px;
  }
  .back-mark__dot {
    width: 58px; height: 58px; border-radius: 50%; background: var(--card-white);
  }
  .back-web {
    position: absolute; right: 48px; bottom: 36px;
    color: var(--card-white); font-size: 17px; letter-spacing: 4px;
  }

  /* front side */
  .wordmark {
    position: absolute; left: 70px; top: 62px;
    display: flex; align-items: center; gap: 12px;
    color: var(--brand-blue);
    font-weight: 700; font-size: 40px; letter-spacing: 0.5px;
  }
  .wordmark__dot {
    width: 34px; height: 34px; border-radius: 50%; background: var(--brand-blue);
  }
  .person {
    position: absolute; right: 70px; top: 150px; text-align: right;
  }
  .person__name {
    color: var(--brand-blue); font-weight: 700; font-size: 24px; letter-spacing: 0.5px;
  }
  .person__title {
    color: var(--brand-orange); font-weight: 400; font-size: 18px; letter-spacing: 0.5px;
  }
  .contact {
    position: absolute; left: 54px; top: 230px;
    color: var(--text-dark); font-size: 17px; line-height: 1.45;
  }
  .contact__address { margin-bottom: 4px; }
  .contact__grid {
    display: grid; grid-template-columns: 180px auto; column-gap: 30px;
  }
  .contact__item { display: flex; align-items: center; gap: 8px; white-space: nowrap; }
  .contact__icon { width: 16px; height: 16px; fill: var(--brand-blue); flex: none; }
</style>
</head>
<body>
<main class="sheet">

  <section class="card card--back" aria-label="Business card, back">
    <svg class="card__shapes" viewBox="0 0 700 400" preserveAspectRatio="none" aria-hidden="true">
      <defs>
        <linearGradient id="backShade" x1="0" y1="0" x2="1" y2="1">
          <stop offset="0" stop-color="#0b74c8"/>
          <stop offset="1" stop-color="#0862ad"/>
        </linearGradient>
      </defs>
      <rect width="700" height="400" fill="url(#backShade)"/>
    </svg>
    <div class="back-mark"><span class="back-mark__dot"></span><span>VELTA Holdings</span></div>
    <p class="back-web">veltaholdings.com</p>
  </section>

  <section class="card card--front" aria-label="Business card, front">
    <svg class="card__shapes" viewBox="0 0 700 400" preserveAspectRatio="none" aria-hidden="true">
      <defs>
        <linearGradient id="orangeShade" x1="0" y1="0" x2="1" y2="1">
          <stop offset="0" stop-color="#e65a1f"/>
          <stop offset="1" stop-color="#b9441a"/>
        </linearGradient>
        <linearGradient id="whiteShade" x1="0" y1="0" x2="0" y2="1">
          <stop offset="0" stop-color="#ffffff"/>
          <stop offset="1" stop-color="#f1f1f1"/>
        </linearGradient>
      </defs>
      <rect width="700" height="400" fill="url(#whiteShade)"/>
      <path class="swoosh-blue" d="M0 0 H170 Q45 35 0 190 Z" fill="#0a6cbd"/>
      <path class="swoosh-orange" d="M700 170 Q690 370 440 400 H700 Z" fill="url(#orangeShade)"/>
    </svg>

    <div class="wordmark"><span class="wordmark__dot"></span><span>VELTA Holdings</span></div>

    <div class="person">
      <p class="person__name">MARA LINTON</p>
      <p class="person__title">PRESIDENT</p>
    </div>

    <div class="contact">
      <p class="contact__address">2190 Kingsbridge Lane Oakridge, NY 11702</p>
      <div class="contact__grid">
        <p class="contact__item">
          <svg class="contact__icon" viewBox="0 0 16 16" aria-hidden="true"><path d="M2 5c0-2 2-3 6-3s6 1 6 3v1h-3V5H5v1H2zM4 7h8l2 6H2z"/></svg>
          555 0142 7781
        </p>
        <p class="contact__item">
          <svg class="contact__icon" viewBox="0 0 16 16" aria-hidden="true"><path d="M3 6h10v7H3zM5 2h6v3H5zM5 8h6v1H5zM5 10h6v1H5z"/></svg>
          555 0176 4419
        </p>
        <p class="contact__item">
          <svg class="contact__icon" viewBox="0 0 16 16" aria-hidden="true"><path d="M4 1h8v14H4zM5 3v9h6V3z"/></svg>
          555 0198 3264
        </p>
        <p class="contact__item">
          <svg class="contact__icon" viewBox="0 0 16 16" aria-hidden="true"><path d="M1 3h14v10H1zM2 4l6 5 6-5z" fill-rule="evenodd"/></svg>
          mara@veltaholdings.com
        </p>
      </div>
    </div>
  </section>

</main>
</body>
</html>
```